To design a brand identity that is simple and creative with 'Corvane' as the brand name, I like modern simple fonts like helvetica neue, I want to print both sides of the card, I am open to dark front and white back, but the design needs to transfer well to letter heads and email signatures, I am looking for sophisticated and elegant, but open minded about clever and off the wall, I do not do 'boring' Corvane Ventures is the mother company for a small group, specialising in Management & consulting, Software development and construction, we have a high level of integrity, we are transparent and accountable for what we do. my images are provided as a guide only, Im not expecting them to be just copied, Im looking for a creator and passionate thinker, who will put life into their work.

Target Market(s)

usually business minded people who are looking for something different in me, such as leadership, confidence and focus with thinking that is per haps a little outside the box..

Industry/Entity Type

Construction

Requirements
Must have
• clean, minmalistic
Nice to have
• custom logo
Should not have
• boring, traditional

```html
<!DOCTYPE html>
<html lang="en">
<head>
<meta charset="utf-8">
<title>Corvane Ventures – Stationery</title>
<link href="https://fonts.googleapis.com/css2?family=Open+Sans:wght@300;400&display=swap" rel="stylesheet">
<style>
  :root {
    --brand-orange: #e8673a;
    --ink: #1e1e1e;
    --muted: #777777;
    --card-edge: #d6d6d6;
    --paper: #ffffff;
    --haze: #f1f1f1;
  }
  html, body {
    margin: 0;
    padding: 0;
    overflow: hidden;
    background: var(--paper);
  }
  .sheet {
    position: relative;
    width: 849px;
    height: 1200px;
    overflow: hidden;
    background: var(--paper);
    font-family: "Open Sans", "Helvetica Neue", Arial, sans-serif;
    color: var(--ink);
  }
  .brand {
    position: absolute;
    display: flex;
    align-items: center;
    color: var(--brand-orange);
    font-weight: 300;
    line-height: 1;
  }
  .brand__dot {
    border-radius: 50%;
    background: var(--brand-orange);
    flex: none;
  }
  .letterhead__brand { left: 60px; top: 66px; font-size: 44px; gap: 14px; }
  .letterhead__brand .brand__dot { width: 36px; height: 36px; }

  .contact {
    position: absolute;
    text-align: right;
    font-weight: 400;
  }
  .letterhead__contact { right: 58px; top: 69px; font-size: 14px; line-height: 16px; }
  .services { margin-top: 4px; }
  .services .sep { color: var(--brand-orange); }

  .backdrop-circle {
    position: absolute;
    left: 30px;
    top: 800px;
    width: 340px;
    height: 340px;
    border-radius: 50%;
    background: var(--haze);
  }

  .card {
    position: absolute;
    top: 492px;
    width: 357px;
    height: 214px;
    border: 1px solid var(--card-edge);
    background: var(--paper);
    box-sizing: border-box;
  }
  .card--front { left: 49px; }
  .card--back { left: 440px; }

  .card--front .brand { left: 64px; top: 72px; font-size: 52px; gap: 18px; }
  .card--front .brand__dot { width: 40px; height: 40px; }

  .card--back .brand { left: 19px; top: 86px; font-size: 28px; gap: 9px; }
  .card--back .brand__dot { width: 22px; height: 22px; }

  .card__details {
    position: absolute;
    right: 22px;
    top: 66px;
    text-align: right;
    font-size: 8px;
    line-height: 10px;
  }
  .card__email { color: var(--brand-orange); font-size: 11px; line-height: 13px; }
  .card__role { margin-bottom: 8px; }
  .card__services { position: absolute; right: 22px; top: 136px; font-size: 7.5px; }
  .card__services .sep { color: var(--brand-orange); }
</style>
</head>
<body>
<main class="sheet">
  <div class="backdrop-circle" aria-hidden="true"></div>

  <header class="letterhead">
    <div class="brand letterhead__brand"><span class="brand__dot"></span><span>corvane.</span></div>
    <div class="contact letterhead__contact">
      <div>M. +61 0400 555 219</div>
      <div>PO BOX 418 Perth 6000</div>
      <div class="services">management <span class="sep">•</span> software <span class="sep">•</span> construction</div>
    </div>
  </header>

  <section class="card card--front" aria-label="Business card front">
    <div class="brand"><span class="brand__dot"></span><span>corvane.</span></div>
  </section>

  <section class="card card--back" aria-label="Business card back">
    <div class="brand"><span class="brand__dot"></span><span>corvane.</span></div>
    <div class="card__details">
      <div class="card__email">adam@corvane.ventures</div>
      <div class="card__role">client ambassador</div>
      <div>M. +61 0400 555 219</div>
      <div>PO BOX 418 Perth 6000</div>
    </div>
    <div class="card__services">management <span class="sep">•</span> software <span class="sep">•</span> construction</div>
  </section>
</main>
</body>
</html>
```